Maple Sprout Menu (Vegetarian Restaurant Concept)

Maple Sprout is a new concept fast casual restaurant
renders are attached so you can see the style of restaurant
Maple Sproute is a vibrant and modern Vegetarian fast casual restaurant concept that mixes fresh food, energy, great décor, and a comfortable, welcoming atmosphere to provide a memorable and all Vegetarian dining experience.
Our Mission is to be top of mind when consumers think Vegetarian food!
Updates
Need extra days to review
Target Market(s)
the menu is vegetarian and appeals to a broad demographic in USA
Font styles to use
Colors
Designer to choose colors to be used in the design.
Requirements
Must have
- well colored and well laid out menu - should not be cartoonish
Nice to have
- For Phots please use the shots in this file:
- https://www.filecrate-share.net/sh/qtrv8knw2lpa5zc/BBBxR_pLmNoQwEE4J_TKX_Va?dl=0
- note these are untouched and you are free to change as needed
Should not have
- Should not be cartoonish - nor kives, forks etc in the design

```html
<!DOCTYPE html>
<html lang="en">
<head>
<meta charset="utf-8">
<title>Maple Sproute Menu</title>
<link rel="stylesheet" href="https://fonts.googleapis.com/css2?family=Josefin+Sans:wght@400;600;700&family=Quicksand:wght@400;500&display=swap">
<style>
  :root {
    --paper: #ffffff;
    --heading-green: #5f8a23;
    --title-green: #1f3a18;
    --body-text: #5a6254;
    --price-text: #4a4f46;
    --rule-dots: #9bbf8c;
    --column-rule: #8fd39a;
    --frame-dots: #78a04a;
    --ornament-fill: #e6efd9;
    --brand-dot: #e99a4e;
  }
  * { margin: 0; padding: 0; box-sizing: border-box; }
  html, body { width: 1200px; height: 927px; overflow: hidden; background: var(--paper); }
  .menu { position: relative; width: 1200px; height: 927px; background: var(--paper); }

  .column-rule {
    position: absolute; top: 12px; width: 0; height: 910px;
    border-left: 1px dashed var(--column-rule);
  }
  .column-rule--first { left: 413px; }
  .column-rule--second { left: 795px; }

  .column { position: absolute; top: 0; height: 927px; }
  .column--left { left: 30px; width: 382px; }
  .column--middle { left: 416px; width: 379px; }
  .column--right { left: 797px; width: 380px; }

  .section { position: absolute; left: 0; right: 0; text-align: center; }

  .section-heading {
    display: inline-block;
    border: 1px dotted var(--frame-dots);
    padding: 0 13px;
    height: 49px;
    font-family: "Josefin Sans", sans-serif;
    font-weight: 400;
    font-size: 21px;
    letter-spacing: 2.6px;
    line-height: 52px;
    color: var(--heading-green);
  }
  .section-heading--double {
    height: 69px; padding: 6px 18px 0; line-height: 27px;
  }

  .items { list-style: none; margin-top: var(--gap, 9px); }
  .item { padding: 10px 0 7px; }
  .item + .item { border-top: 1px dotted var(--rule-dots); }

  .item-title {
    font-family: "Josefin Sans", sans-serif;
    font-weight: 700;
    font-size: 12.5px;
    letter-spacing: 2.2px;
    line-height: 21.5px;
    color: var(--title-green);
    white-space: nowrap;
  }
  .item-desc {
    margin-top: 6px;
    font-family: "Quicksand", sans-serif;
    font-weight: 400;
    font-size: 13px;
    letter-spacing: 0.7px;
    line-height: 21px;
    color: var(--body-text);
    white-space: nowrap;
  }
  .item-price {
    margin-top: 5px;
    font-family: "Quicksand", sans-serif;
    font-weight: 500;
    font-size: 13px;
    letter-spacing: 0.5px;
    line-height: 18px;
    color: var(--price-text);
  }
  .item--plain .item-price { margin-top: 9px; }

  .closing-rule {
    position: absolute; left: 7px; top: 782px; width: 370px; height: 4px;
    background: radial-gradient(circle, var(--heading-green) 1.3px, transparent 1.6px) 0 0 / 9.3px 4px repeat-x;
  }
  .tagline {
    position: absolute; left: 0; right: 0; top: 803px; text-align: center;
    font-family: "Josefin Sans", sans-serif;
    font-size: 17px; letter-spacing: 1.1px; line-height: 34px;
    color: var(--heading-green);
  }
  .website {
    position: absolute; left: 105px; top: 889px; width: 168px; text-align: center;
    font-family: "Josefin Sans", sans-serif;
    font-size: 11px; letter-spacing: 2.6px; line-height: 14px;
    color: var(--heading-green);
    border-bottom: 1px solid var(--heading-green);
    padding-bottom: 3px;
  }

  .brand-block { position: absolute; left: 0; right: 0; top: 360px; height: 138px; }
  .brand-ornament {
    position: absolute; top: 0; width: 70px; height: 138px;
    background: var(--ornament-fill);
  }
  .brand-ornament--left { left: 40px; }
  .brand-ornament--right { left: 269px; }
  .brand-mark {
    position: absolute; left: 50%; top: 14px; transform: translateX(-50%);
    width: 44px; height: 44px; border-radius: 50%;
    background: var(--brand-dot);
  }
  .brand-name {
    position: absolute; left: 115px; right: 115px; top: 84px; text-align: center;
    font-family: "Quicksand", sans-serif;
    font-weight: 500;
    font-size: 18px; letter-spacing: 0.3px; line-height: 24px;
    color: var(--title-green);
    white-space: nowrap;
  }
</style>
</head>
<body>
<main class="menu">
  <div class="column-rule column-rule--first"></div>
  <div class="column-rule column-rule--second"></div>

  <!-- Left column -->
  <div class="column column--left">
    <section class="section" style="top:29px; --gap:9px">
      <h2 class="section-heading">SALADS</h2>
      <ul class="items">
        <li class="item">
          <h3 class="item-title">BRUSSEL SPROUT CAESAR</h3>
          <p class="item-desc">little gem romaine, toasted torn bread,<br>parmigiano reggiano</p>
          <p class="item-price">8.99</p>
        </li>
        <li class="item">
          <h3 class="item-title">HEIRLOOM BEET SALAD</h3>
          <p class="item-desc">shaved chioggia beet, roasted golden beet, red<br>quinoa, little gem, arugula, lemon vinaigrette</p>
          <p class="item-price">8.99</p>
        </li>
        <li class="item">
          <h3 class="item-title">ZESTY BLACK BEAN &amp; CORN SALAD IN<br>LETTUCE CUPS</h3>
          <p class="item-desc">black beans, avocado &amp; roasted corn topped with<br>feta crumbles in butter lettuce</p>
          <p class="item-price">8.99</p>
        </li>
        <li class="item">
          <h3 class="item-title">GREEN, RED AND WHITE</h3>
          <p class="item-desc">spring leaves, cherry tomatoes, avocado, roasted<br>almond &amp; goat cheese</p>
          <p class="item-price">8.99</p>
        </li>
      </ul>
    </section>

    <section class="section" style="top:567px; --gap:11px">
      <h2 class="section-heading">SOUP</h2>
      <ul class="items">
        <li class="item item--plain">
          <h3 class="item-title">BLACK BEAN CHOWDER</h3>
          <p class="item-price">8.99</p>
        </li>
        <li class="item item--plain">
          <h3 class="item-title">QUINOA AND VEGETABLE SOUP</h3>
          <p class="item-price">8.99</p>
        </li>
      </ul>
    </section>

    <div class="closing-rule"></div>
    <p class="tagline">‘revolutionizing the vegetarian<br>food experience’</p>
    <p class="website">www.maplesproute.com</p>
  </div>

  <!-- Middle column -->
  <div class="column column--middle">
    <section class="section" style="top:29px; --gap:9px">
      <h2 class="section-heading">TOASTS</h2>
      <ul class="items">
        <li class="item">
          <h3 class="item-title">EVERYTHING AVOCADO TOAST</h3>
          <p class="item-desc">avocado on whole grain toast with our signature<br>spice blend</p>
          <p class="item-price">8.99</p>
        </li>
        <li class="item item--plain">
          <h3 class="item-title">TOMATO &amp; BEET BRUSCHETTA</h3>
          <p class="item-price">8.99</p>
        </li>
        <li class="item item--plain">
          <h3 class="item-title">VEGETABLE MELT ON GARLIC TOAST</h3>
          <p class="item-price">8.99</p>
        </li>
      </ul>
    </section>

    <div class="brand-block">
      <div class="brand-ornament brand-ornament--left" role="img" aria-label="Decorative green dotted line ornament"></div>
      <div class="brand-ornament brand-ornament--right" role="img" aria-label="Decorative green dotted line ornament"></div>
      <div class="brand-mark"></div>
      <p class="brand-name">Maple Sproute</p>
    </div>

    <section class="section" style="top:536px; --gap:13px">
      <h2 class="section-heading">BOWLS</h2>
      <ul class="items">
        <li class="item item--plain">
          <h3 class="item-title">ROASTED VEGETABLE, &amp; SPINACH BOWL</h3>
          <p class="item-price">8.99</p>
        </li>
        <li class="item item--plain">
          <h3 class="item-title">SUGAR SNAP PEA &amp; CARROT SOBA<br>NOODLES</h3>
          <p class="item-price">8.99</p>
        </li>
        <li class="item item--plain">
          <h3 class="item-title">WHOLE GRAIN &amp; VEGETABLE BUDDHA<br>BOWL</h3>
          <p class="item-price">8.99</p>
        </li>
        <li class="item item--plain">
          <h3 class="item-title">ORANGE &amp; PISTACHIO QUINOA</h3>
          <p class="item-price">8.99</p>
        </li>
      </ul>
    </section>
  </div>

  <!-- Right column -->
  <div class="column column--right">
    <section class="section" style="top:26px; --gap:12px">
      <h2 class="section-heading section-heading--double">BURGERS, WRAPS &amp;<br>SANDWICHES</h2>
      <ul class="items">
        <li class="item item--plain">
          <h3 class="item-title">SWEET POTATO, BLACK BEAN VEGGIE<br>BURGERS WITH CABBAGE-PEPITA SLAW</h3>
          <p class="item-price">8.99</p>
        </li>
        <li class="item item--plain">
          <h3 class="item-title">ROASTED VEGGIE, ARUGULA &amp; HUMMUS<br>WRAPS</h3>
          <p class="item-price">8.99</p>
        </li>
        <li class="item item--plain">
          <h3 class="item-title">GARDEN BURGER</h3>
          <p class="item-price">8.99</p>
        </li>
        <li class="item">
          <h3 class="item-title">BEANS &amp; GREENS QUESADILLAS</h3>
          <p class="item-desc">greens, Mexican cheese, beans &amp; avocado, with<br>salsa</p>
          <p class="item-price">8.99</p>
        </li>
        <li class="item">
          <h3 class="item-title">VEGGIE BURRITO</h3>
          <p class="item-desc">greens, Mexican cheese, beans, brown rice,<br>roasted chili corn &amp; avocado, with ancho chili<br>salsa, wheat tortilla</p>
          <p class="item-price">8.99</p>
        </li>
      </ul>
    </section>

    <section class="section" style="top:628px; --gap:13px">
      <h2 class="section-heading">DESSERT</h2>
      <ul class="items">
        <li class="item item--plain">
          <h3 class="item-title">STRAWBERRY BALSAMIC ICE CREAM<br>SUNDAE</h3>
          <p class="item-price">8.99</p>
        </li>
        <li class="item item--plain">
          <h3 class="item-title">EXOTIC FRUIT BOWL</h3>
          <p class="item-price">8.99</p>
        </li>
        <li class="item item--plain">
          <h3 class="item-title">WHITE AND DARK OATMEAL COOKIE</h3>
          <p class="item-price">8.99</p>
        </li>
      </ul>
    </section>
  </div>
</main>
</body>
</html>
```